Heron Loan Partners Business Card

We need a business card design for our mortgage servicing company. In addition to servicing the loans of homeowners, we help homeowners with purchasing their homes and any mortgage refinancing. We would like to see designs that use the colors in the logo attached below (gold-ish yellow and navy blue), and any other design you deem fit! The design should communicate a simpler life with smart mortgages provided by Heron.

```html
<!DOCTYPE html>
<html lang="en">
<head>
<meta charset="utf-8">
<title>Heron Loan Partners – Business Card</title>
<link href="https://fonts.googleapis.com/css2?family=Arimo:wght@400;700&display=swap" rel="stylesheet">
<style>
  :root {
    --navy: #241f52;
    --gold: #cfa633;
    --paper: #f6f6f7;
    --ink: #2b2b2b;
    --backdrop: #e4e4e6;
  }
  * { margin: 0; padding: 0; box-sizing: border-box; }
  html, body { width: 1200px; height: 912px; overflow: hidden; }
  body {
    background: var(--backdrop);
    font-family: "Arimo", Arial, sans-serif;
    position: relative;
  }
  .card {
    position: absolute;
    width: 540px;
    height: 310px;
    border-radius: 3px;
    box-shadow: 0 10px 28px rgba(0,0,0,0.22);
    overflow: hidden;
  }
  /* Front */
  .card-front {
    left: 70px; top: 90px;
    background: var(--navy);
  }
  .front-brand {
    position: absolute;
    left: 0; right: 0; top: 118px;
    text-align: center;
    color: var(--gold);
    font-weight: 700;
    font-size: 38px;
    letter-spacing: 0.5px;
  }
  .front-web {
    position: absolute;
    left: 0; right: 0; top: 228px;
    text-align: center;
    color: #ffffff;
    font-size: 15px;
    letter-spacing: 3px;
  }
  .front-web .accent { color: var(--gold); }

  /* Back */
  .card-back {
    left: 600px; top: 490px;
    background: var(--paper);
  }
  .back-brand {
    position: absolute;
    right: 60px; top: 46px;
    color: var(--gold);
    font-weight: 700;
    font-size: 22px;
  }
  .divider {
    position: absolute;
    left: 40px; right: 28px; top: 116px;
    height: 1px;
    background: var(--ink);
  }
  .contact-list {
    position: absolute;
    right: 28px; top: 128px;
    list-style: none;
    text-align: right;
    color: var(--ink);
    font-size: 13px;
    line-height: 19px;
  }
  .contact-list li { display: flex; justify-content: flex-end; align-items: center; gap: 6px; }
  .contact-list svg { width: 11px; height: 11px; }
  .person {
    position: absolute;
    left: 36px; top: 192px;
  }
  .person-name { color: var(--gold); font-weight: 700; font-size: 21px; }
  .person-title { color: var(--navy); font-size: 15px; margin-top: 1px; }
  .address {
    margin-top: 14px;
    color: var(--ink);
    font-size: 14px;
    line-height: 18px;
  }
  .band-gold {
    position: absolute;
    left: 0; bottom: 14px;
    width: 79%; height: 13px;
    background: var(--gold);
  }
  .band-navy {
    position: absolute;
    left: 79%; right: 0; bottom: 27px;
    height: 13px;
    background: var(--navy);
  }
</style>
</head>
<body>

<section class="card card-front" aria-label="Card front">
  <div class="front-brand">Heron Loan Partners</div>
  <div class="front-web">www.<span class="accent">Heron</span>.com</div>
</section>

<section class="card card-back" aria-label="Card back">
  <div class="back-brand">Heron Loan Partners</div>
  <div class="divider"></div>

  <ul class="contact-list">
    <li>(555) 0142-7781
      <svg viewBox="0 0 12 12" aria-hidden="true"><path d="M2 1 L4.5 1 L5.5 3.5 L4 4.5 Q5 7 7.5 8 L8.5 6.5 L11 7.5 L11 10 Q6 11 3 8 Q0.5 5 2 1 Z" fill="var(--gold)"/></svg>
    </li>
    <li>name@Heron.com
      <svg viewBox="0 0 12 12" aria-hidden="true"><rect x="0.5" y="2.5" width="11" height="7" fill="var(--gold)"/><path d="M0.5 2.5 L6 6.5 L11.5 2.5" stroke="#fff" stroke-width="1" fill="none"/></svg>
    </li>
    <li>www.Heron.com
      <svg viewBox="0 0 12 12" aria-hidden="true"><circle cx="6" cy="6" r="5.5" fill="var(--gold)"/><ellipse cx="6" cy="6" rx="2.2" ry="5.5" stroke="#fff" stroke-width="0.8" fill="none"/><line x1="0.5" y1="6" x2="11.5" y2="6" stroke="#fff" stroke-width="0.8"/></svg>
    </li>
  </ul>

  <div class="person">
    <div class="person-name">Daniel Rowe</div>
    <div class="person-title">President</div>
    <div class="address">1270 Alder Crest Lane<br>Brookvale, NY 11290</div>
  </div>

  <div class="band-gold"></div>
  <div class="band-navy"></div>
</section>

</body>
</html>
```